Brochure Design Project

PAMT
The brochure is intended to be on Pacific Alliance of Mindful Therapies website available for the members to download for the purpose of educating public about benefits of clinical hypnosis and introduce it as possible treatment option. There should be a empty space left on the last page for the member to stamp their office information.
So, the intended audience is general public that might be interested in hypnosis treatment
White on blue is logo of PAMT.
I would like the brochure to have bright complimentary colors with imagery that is used in health care/complimentary medicine - nature, relaxation, etc.
PAMT website is PAMTweb.net.

```html
<!DOCTYPE html>
<html lang="en">
<head>
<meta charset="utf-8">
<title>PAMT Brochure – Outside Spread</title>
<link rel="stylesheet" href="https://fonts.googleapis.com/css2?family=Nunito:ital,wght@0,600;0,700;1,700;1,800&family=Open+Sans:wght@600&family=Libre+Baskerville:wght@700&display=swap">
<style>
  :root{
    --page:#ffffff;
    --sky:#bfe3f2;
    --mist:#e6f4f8;
    --leaf:#55a745;
    --orange:#e8542a;
    --sun:#f1b72b;
    --rose:#e7265f;
    --ocean:#3b8bcb;
    --navy:#1f2a6b;
    --ink:#333333;
    --frame:#d9d9d9;
    --social:#5b7fa8;
  }
  *{margin:0;padding:0;box-sizing:border-box}
  html,body{width:1200px;height:947px;overflow:hidden;background:var(--page)}
  .spread{position:relative;width:1200px;height:947px;background:var(--page)}
  .wash{
    position:absolute;left:44px;top:44px;width:1112px;height:858px;
    background:
      radial-gradient(ellipse 520px 360px at 10% 8%, #a9d9ee 0%, rgba(169,217,238,0) 70%),
      radial-gradient(ellipse 560px 320px at 70% 12%, #cfeaf4 0%, rgba(207,234,244,0) 70%),
      radial-gradient(ellipse 500px 300px at 35% 95%, #e4f3f0 0%, rgba(228,243,240,0) 70%),
      linear-gradient(180deg, var(--mist) 0%, #f7fbfc 60%, #f2f8f6 100%);
  }
  .panel{
    position:absolute;left:59px;width:349px;background:var(--leaf);color:#fff;
    font-family:"Open Sans",Arial,sans-serif;font-weight:600;font-size:14.4px;line-height:22.6px;
    text-align:justify;padding:8px 12px 12px 12px;hyphens:auto;
  }
  .panel--worry{top:58px;height:234px}
  .panel--practice{top:308px;height:317px;padding-top:14px}
  .panel__title{
    font-family:"Nunito",sans-serif;font-style:italic;font-weight:800;font-size:31px;
    line-height:38px;margin:0 0 20px 6px;text-align:left;
  }
  .stamp-box{
    position:absolute;left:86px;top:652px;width:294px;height:214px;
    border:1.5px solid var(--frame);border-radius:22px;
    font-family:"Open Sans",Arial,sans-serif;font-size:10.5px;color:var(--ink);
    text-align:center;padding-top:5px;line-height:20px;font-weight:600;
  }
  .stamp-box small{font-size:9.5px;display:block}
  .brand{position:absolute;text-align:center;color:var(--navy)}
  .brand__name{
    display:inline-flex;align-items:center;gap:10px;
    font-family:"Nunito",sans-serif;font-weight:700;font-size:44px;line-height:54px;letter-spacing:3px;
  }
  .brand__mark{width:14px;height:14px;background:var(--navy);display:inline-block}
  .brand__full{
    font-family:"Libre Baskerville",Georgia,serif;font-weight:700;font-size:12.4px;
    letter-spacing:0.2px;margin-top:4px;white-space:nowrap;
  }
  .brand--cover{left:826px;top:136px;width:296px}
  .brand--back{left:456px;top:730px;width:296px}
  .ribbons{position:absolute;left:0;top:0}
  .ribbons text{font-family:"Nunito",sans-serif;font-weight:600;fill:#fff;font-size:31px}
  .ribbons .question{font-style:italic;font-weight:700}
  .social{position:absolute;left:492px;top:840px;display:flex;gap:7px}
  .social__item{width:29px;height:29px;border-radius:5px;background:var(--social)}
  .site-url{
    position:absolute;right:44px;top:851px;font-family:"Open Sans",Arial,sans-serif;
    font-weight:600;font-size:13px;color:var(--ink);
  }
</style>
</head>
<body>
<main class="spread">
  <div class="wash" role="img" aria-label="Soft sky-blue watercolour wash background"></div>

  <section class="panel panel--worry">
    <p>People are also worried that their problems cannot be helped.</p>
    <p>Hypnosis might offer a novel way to approach or resolve the problem, or just see it in a different light.</p>
    <p>Even if hypnosis does not immediately solve the problem, you can still learn how to be a little more comfortable and experience a deeper level of physical and mental relaxation.</p>
  </section>

  <section class="panel panel--practice">
    <h2 class="panel__title">Practice will help.</h2>
    <p>Well-trained medical or mental health professionals will help you discover and use resources and strengths that you did not know you had.</p>
    <p>Your therapist, doctor or dentist might be the best person to discuss hypnosis and how it can be helpful to you.</p>
    <p>Licensed professionals get their training and certification through the Pacific Alliance of Mindful Therapies. You can find a list of certified providers on PAMTweb.net.</p>
  </section>

  <div class="stamp-box">Information about your professional<small>(stamp or printed)</small></div>

  <svg class="ribbons" width="1200" height="947" viewBox="0 0 1200 947" aria-hidden="false">
    <defs>
      <linearGradient id="shade" x1="0" x2="1" y1="0" y2="0">
        <stop offset="0" stop-color="#000" stop-opacity="0.12"/>
        <stop offset="0.95" stop-color="#000" stop-opacity="0.04"/>
        <stop offset="1" stop-color="#000" stop-opacity="0"/>
      </linearGradient>
    </defs>
    <g class="ribbon ribbon--what">
      <polygon points="414,384 756,239 1104,239 1140,282 1104,324 756,324 414,414" fill="var(--orange)"/>
      <polygon points="414,384 756,239 756,324 414,414" fill="url(#shade)"/>
      <text x="1068" y="292" text-anchor="end">What</text>
    </g>
    <g class="ribbon ribbon--why">
      <polygon points="414,420 756,335 1104,335 1140,378 1104,420 756,420 414,452" fill="var(--sun)"/>
      <polygon points="414,420 756,335 756,420 414,452" fill="url(#shade)"/>
      <text x="1068" y="390" text-anchor="end">Why</text>
    </g>
    <g class="ribbon ribbon--when">
      <polygon points="414,458 756,430 1104,430 1140,473 1104,516 756,516 414,492" fill="var(--rose)"/>
      <polygon points="414,458 756,430 756,516 414,492" fill="url(#shade)"/>
      <text x="1068" y="485" text-anchor="end">When</text>
    </g>
    <g class="ribbon ribbon--how">
      <polygon points="414,498 756,526 1104,526 1140,569 1104,612 756,612 414,532" fill="var(--ocean)"/>
      <polygon points="414,498 756,526 756,612 414,532" fill="url(#shade)"/>
      <text x="1068" y="581" text-anchor="end">How</text>
    </g>
    <g class="ribbon ribbon--fit">
      <polygon points="414,538 756,620 1104,620 1140,664 1104,708 756,708 414,626" fill="var(--leaf)"/>
      <polygon points="414,538 756,620 756,708 414,626" fill="url(#shade)"/>
      <text class="question" x="1068" y="656" text-anchor="end">Could it be right</text>
      <text class="question" x="1068" y="694" text-anchor="end">for me?</text>
    </g>
  </svg>

  <div class="brand brand--cover">
    <div class="brand__name"><span class="brand__mark"></span>PAMT</div>
    <div class="brand__full">PACIFIC ALLIANCE OF MINDFUL THERAPIES</div>
  </div>

  <div class="brand brand--back">
    <div class="brand__name"><span class="brand__mark"></span>PAMT</div>
    <div class="brand__full">PACIFIC ALLIANCE OF MINDFUL THERAPIES</div>
  </div>

  <div class="social" aria-label="Social media links">
    <span class="social__item"></span><span class="social__item"></span><span class="social__item"></span>
    <span class="social__item"></span><span class="social__item"></span><span class="social__item"></span>
  </div>

  <div class="site-url">http://www.pamtweb.net</div>
</main>
</body>
</html>
```